Website for my photography business

I need a website for my photography business, Bram Kellet Photography. I need a website that has a landing page with a cover photo of each kind of photography I do. For example, Nature, Weddings, Portraits and Architecture. I want it so that when someone comes onto my website they have to choose which kind of photography page they want to visit. So if they click on the wedding photo it will open to a page with my wedding portfolio images and a contact me button. If they choose nature photography I want them to be redirected to an e-commerce section where they can purchase prints. Architecture and Portraits should open up to their respective portfolios with about me and contact info. I like this kind of format because I want people who come to my website for a specific type of photography to be able to be directed there easily without having to look at a mix of other kinds of photography. I will provide a few files to use as placeholders. I have already purchased the bramkelletphotography.example domain name. A Wix website would be great because I am most familiar with it but I am open to anything.

Industry/Entity Type

Photographer

Number of Pages Required

5+ page

Requirements
Must have
• Landing Page and e-commerce

```html
<!DOCTYPE html>
<html lang="en">
<head>
<meta charset="utf-8">
<title>Bram Kellet Photography</title>
<link rel="stylesheet" href="https://fonts.googleapis.com/css2?family=Questrial&family=Great+Vibes&display=swap">
<style>
  :root {
    --navy: #1d2552;
    --gold: #e9a21a;
    --ink: #2f2f35;
    --cream: #fbe5c3;
    --white: #ffffff;
  }
  * { box-sizing: border-box; margin: 0; padding: 0; }
  html, body { width: 1200px; height: 2246px; overflow: hidden; }
  body {
    position: relative;
    background: var(--white);
    font-family: "Questrial", "Century Gothic", sans-serif;
    color: var(--navy);
  }
  a { color: inherit; text-decoration: none; }

  .hero {
    position: absolute; left: 0; top: 0; width: 1200px; height: 644px;
  }
  .hero-photo {
    position: absolute; inset: 0;
    background: linear-gradient(180deg, #86b4b6 0%, #a9c8bd 28%, #cfd4b4 52%, #dcc59b 74%, #b8935f 100%);
  }
  .brand {
    position: absolute; left: 111px; top: 40px;
    font-size: 22px; line-height: 28px; color: var(--navy); letter-spacing: 0.3px;
  }
  .main-nav { position: absolute; top: 42px; left: 0; width: 1200px; font-size: 17px; line-height: 22px; }
  .main-nav a { position: absolute; white-space: nowrap; }
  .main-nav .is-current { color: var(--gold); }

  .hero-title {
    position: absolute; left: 109px; top: 246px;
    font-family: "Great Vibes", cursive; font-size: 56px; line-height: 70px; font-weight: 400;
    color: var(--navy); white-space: nowrap;
  }
  .hero-tagline {
    position: absolute; left: 154px; top: 341px;
    font-size: 18px; line-height: 24px; color: var(--navy); white-space: nowrap;
  }

  .category { position: absolute; width: 391px; text-align: center; }
  .category-number {
    display: block; text-align: left; font-size: 14px; line-height: 16px; height: 23px; color: var(--gold);
  }
  .category-photo { width: 391px; height: 477px; }
  .category-title { margin-top: 17px; font-size: 21px; line-height: 26px; font-weight: 400; color: var(--navy); letter-spacing: 0.3px; }
  .category-link { display: inline-block; margin-top: 2px; font-size: 13px; line-height: 18px; text-decoration: underline; color: var(--navy); }

  .photo-nature { background: linear-gradient(160deg, #2c3a3a 0%, #4b5a45 40%, #c27a3c 62%, #e8edf3 80%, #f5f7fa 100%); }
  .photo-weddings { background: linear-gradient(150deg, #a9a7b3 0%, #8a87a0 35%, #2a2d55 55%, #8d8a9e 75%, #c6c0b4 100%); }
  .photo-portraits { background: linear-gradient(140deg, #3a3a3a 0%, #8a8a8a 35%, #c9c9c9 55%, #6e6e6e 80%, #2e2e2e 100%); }
  .photo-architecture { background: linear-gradient(180deg, #c9cbcc 0%, #a4735c 35%, #b8aa98 60%, #8d8f8c 85%, #a6a7a2 100%); }

  .site-footer {
    position: absolute; left: 0; top: 2086px; width: 1200px; height: 160px;
    background: var(--cream); color: var(--ink); font-size: 18px;
  }
  .copyright { position: absolute; left: 111px; top: 57px; line-height: 26px; }
  .social-links a { position: absolute; top: 72px; line-height: 24px; white-space: nowrap; }
</style>
</head>
<body>

<header class="hero">
  <div class="hero-photo" role="img" aria-label="Cover photo: an elephant sitting on a bare tree branch above desert dunes under a teal sky"></div>
  <a class="brand" href="#">Bram Kellet Photography</a>
  <nav class="main-nav">
    <a class="is-current" href="#" style="left:657px">Home</a>
    <a href="#" style="left:732px">About</a>
    <a href="#" style="left:809px">Categories</a>
    <a href="#" style="left:924px">Portfolio</a>
    <a href="#" style="left:1021px">Contact</a>
  </nav>
  <h1 class="hero-title">Bram Kellet Photography</h1>
  <p class="hero-tagline">Creating Extraordinary Images That Lost Infinetly</p>
</header>

<main>
  <article class="category" style="left:154px; top:760px">
    <span class="category-number">01</span>
    <div class="category-photo photo-nature" role="img" aria-label="Nature cover photo: a red fox sitting in snow among evergreen trees"></div>
    <h2 class="category-title">NATURE</h2>
    <a class="category-link" href="#">SEE MORE</a>
  </article>

  <article class="category" style="left:655px; top:717px">
    <span class="category-number">02</span>
    <div class="category-photo photo-weddings" role="img" aria-label="Weddings cover photo: a dark wedding band and a gold diamond ring resting on granite"></div>
    <h2 class="category-title">WEDDINGS</h2>
    <a class="category-link" href="#">SEE MORE</a>
  </article>

  <article class="category" style="left:154px; top:1384px">
    <span class="category-number">03</span>
    <div class="category-photo photo-portraits" role="img" aria-label="Portraits cover photo: black and white close study of folded arms"></div>
    <h2 class="category-title">PORTRAITS</h2>
    <a class="category-link" href="#">SEE MORE</a>
  </article>

  <article class="category" style="left:655px; top:1445px">
    <span class="category-number">04</span>
    <div class="category-photo photo-architecture" role="img" aria-label="Architecture cover photo: a modern brick and stone building with glass balconies"></div>
    <h2 class="category-title">ARCHITECTURE</h2>
    <a class="category-link" href="#">SEE MORE</a>
  </article>
</main>

<footer class="site-footer">
  <p class="copyright">Copyrights @ 2020 Bram Kellet Photography.<br>All Rights Reserved.</p>
  <nav class="social-links">
    <a href="#" style="left:710px">Facepage</a>
    <a href="#" style="left:873px">Snapgram</a>
    <a href="#" style="left:1035px">Chirper</a>
    <a href="#" style="left:1125px">C20</a>
  </nav>
</footer>

</body>
</html>
```